RM Installations Web Site Design

Need a basic site to show clients a little about what we do. We are a custom audio video company in the high-end residential market. Need a few basic but professional pages to show past projects and products we sell. No e-commerce. Should include my new logo from MarkBazaar.

Industry/Entity Type

Residential

Number of Pages Required

2 page

Font styles to use
Serif
Sans Serif

Colors
f78f20

Requirements
Must have
• Company Logo, Send feedback page
Nice to have
• I have no ideas about design, but I do know what I like and dislike when I see it.

```html
<!DOCTYPE html>
<html lang="en">
<head>
<meta charset="utf-8">
<title>RM Installations</title>
<link href="https://fonts.googleapis.com/css2?family=Roboto:wght@400;700&family=Roboto+Condensed:wght@400;700&family=Lato:ital,wght@0,400;0,700;1,700&display=swap" rel="stylesheet">
<style>
:root{
  --orange:#f78f20;
  --orange-dark:#e07a10;
  --ink:#222;
  --text:#444;
  --muted:#666;
  --grey-bg:#f6f6f6;
  --line:#ddd;
  --footer:#050505;
  --panel:#444;
}
*{box-sizing:border-box;margin:0;padding:0}
html,body{width:674px;height:1200px;overflow:hidden;background:#fff}
body{position:relative;font-family:"Lato",sans-serif;color:var(--text)}
.abs{position:absolute}

/* header */
.site-header{left:0;top:0;width:674px;height:68px;border-top:2px solid var(--orange);background:linear-gradient(#fff,#eee)}
.brand{left:74px;top:12px;display:flex;align-items:center;gap:6px}
.brand-mark{width:28px;height:28px;background:var(--ink)}
.brand-name{font-family:"Roboto",sans-serif;font-size:12px;font-weight:700;color:var(--ink);letter-spacing:.3px}
.call{left:508px;top:16px;display:flex;align-items:center;gap:5px}
.call-text small{display:block;font-size:7.5px;color:var(--muted)}
.call-text b{font-family:"Roboto",sans-serif;font-size:12px;font-weight:400;color:var(--ink)}

/* nav */
.main-nav{left:74px;top:56px;height:24px;display:flex;background:linear-gradient(#fff,#ececec);box-shadow:0 1px 3px rgba(0,0,0,.3);z-index:2}
.nav-home{width:29px;background:var(--ink);display:flex;align-items:center;justify-content:center}
.nav-home span{width:11px;height:11px;background:var(--orange)}
.nav-item{font-family:"Roboto Condensed",sans-serif;font-weight:700;font-size:8px;color:var(--ink);display:flex;align-items:center;justify-content:center;border-right:1px solid var(--line)}

/* hero */
.hero{left:0;top:68px;width:674px;height:250px;background:linear-gradient(180deg,#ef8a1f 0%,#f59a2e 60%,#c94a2a 85%,#eee 100%)}
.hero-caption{left:0;top:294px;width:674px;height:24px;background:rgba(247,143,32,.9);font-family:"Roboto Condensed",sans-serif;font-weight:700;font-size:12px;color:#2a1a0a;text-align:center;line-height:24px}
.hero-arrow{top:301px;width:10px;height:10px;border-radius:50%;background:#f5c690}

/* sections */
.section-title{left:0;width:674px;text-align:center;font-family:"Roboto",sans-serif;font-weight:700;color:var(--ink)}
.section-title em{font-style:normal;color:var(--orange)}
.divider{left:305px;width:64px;height:8px}
.btn{background:var(--orange);color:#fff;font-size:7px;font-weight:700;display:flex;align-items:center;justify-content:center;border-radius:1px}

.welcome-text{left:76px;top:396px;width:522px;font-size:6.6px;line-height:11.8px;text-align:center;color:var(--text)}

.products{left:0;top:496px;width:674px;height:280px;background:var(--grey-bg);border-top:1px solid #e6e6e6;border-bottom:1px solid #e6e6e6}
.card{top:579px;width:161px;height:143px;background:#fff;border:1px solid #ddd;box-shadow:0 1px 2px rgba(0,0,0,.08)}
.card-photo{position:absolute;left:4px;top:5px;width:151px;height:64px}
.card h3{position:absolute;top:75px;left:0;width:100%;text-align:center;font-family:"Roboto",sans-serif;font-size:9.5px;font-weight:700;color:var(--ink)}
.card p{position:absolute;top:93px;left:6px;width:147px;text-align:center;font-family:"Roboto",sans-serif;font-size:6.6px;line-height:11px;color:var(--text)}
.card .plus{position:absolute;right:7px;bottom:6px;width:10px;height:10px;background:var(--orange)}
.chev{top:638px}

.tile{}

/* footer */
.site-footer{left:0;top:1048px;width:674px;height:126px;background:var(--footer)}
.feedback{left:78px;top:1048px;width:164px;height:114px;background:var(--panel)}
.feedback h4{position:absolute;left:6px;top:4px;font-family:"Lato",sans-serif;font-style:italic;font-weight:700;font-size:8px;color:#fff}
.field{position:absolute;left:6px;width:152px;height:20px;background:#eee;border-radius:2px;font-size:6.5px;color:#888;padding-left:8px;line-height:20px}
.subscribe{position:absolute;left:6px;top:91px;width:53px;height:15px;font-size:7px}
.footer-col h4{font-family:"Roboto Condensed",sans-serif;font-weight:700;font-size:9.5px;color:#fff;padding-bottom:5px;border-bottom:1px solid #333}
.links{left:265px;top:1056px;width:110px}
.links ul{list-style:none;display:grid;grid-template-columns:63px 50px;row-gap:5px;margin-top:7px}
.links li{font-size:6.4px;color:#ccc}
.contact{left:401px;top:1056px;width:188px}
.world-map{left:400px;top:1076px;width:82px;height:76px;background:radial-gradient(#333,#111 70%,transparent 72%)}
.address{left:475px;top:1082px;width:116px;height:34px;background:#1a1a1a;font-size:6.8px;line-height:11px;color:#fff;padding:4px 10px 0 10px}
.contact-line{left:463px;font-size:6.8px;color:#fff;display:flex;align-items:center;gap:6px}
.bottom-bar{left:0;top:1174px;width:674px;height:26px;background:var(--orange)}
.social{top:1179px;width:16px;height:16px;border-radius:50%;background:#fff}
.social.dark{background:#111}
.copyright{left:380px;top:1183px;width:220px;text-align:right;font-size:6.6px;color:#1a1a1a}
</style>
</head>
<body>

<header class="abs site-header"></header>
<div class="abs brand"><span class="brand-mark"></span><span class="brand-name">RM INSTALLATIONS</span></div>
<div class="abs call">
  <svg width="16" height="16" viewBox="0 0 16 16"><circle cx="8" cy="8" r="7" fill="none" stroke="#999" stroke-width="1"/><path d="M5.5 4.5l2 2-1 1c.5 1 1.2 1.7 2 2l1-1 2 2-1.3 1.3C7 11.5 4.5 9 4.2 5.8z" fill="#999"/></svg>
  <div class="call-text"><small>Call Us Today</small><b>0123456789</b></div>
</div>

<nav class="abs main-nav">
  <div class="nav-home"><span></span></div>
  <div class="nav-item" style="width:81px">OUR TEAM</div>
  <div class="nav-item" style="width:78px">PRODUCTS</div>
  <div class="nav-item" style="width:71px">SERVICE</div>
  <div class="nav-item" style="width:100px">PAST PROJECT</div>
  <div class="nav-item" style="width:81px">FEEDBACK</div>
  <div class="nav-item" style="width:87px;border-right:0">CONTACT US</div>
</nav>

<div class="abs hero" role="img" aria-label="Home theatre room with wall-mounted TV, speakers and red lounge chairs against an orange wall"></div>
<div class="abs hero-caption">Whole-House Control Systems</div>
<svg class="abs hero-arrow" style="left:79px" viewBox="0 0 10 10"><path d="M6 2.5L3.5 5 6 7.5" fill="none" stroke="#c96a10" stroke-width="1.4"/></svg>
<svg class="abs hero-arrow" style="left:585px" viewBox="0 0 10 10"><path d="M4 2.5L6.5 5 4 7.5" fill="none" stroke="#c96a10" stroke-width="1.4"/></svg>

<!-- welcome -->
<h1 class="abs section-title" style="top:344px;font-size:17.5px">WECLOME TO <em>RM INSTALLATIONS</em></h1>
<svg class="abs divider" style="top:374px" viewBox="0 0 64 8"><line x1="0" y1="4" x2="64" y2="4" stroke="#ccc"/><rect x="28" y="0" width="8" height="8" transform="rotate(45 32 4)" fill="#ddd"/></svg>
<p class="abs welcome-text">Lorem ipsum dolor sit amet, consectetuer adipiscing elit, sed diam nonummy nibh euismod tincidunt ut laoreet dolore magna aliquam erat volutpat. Ut wisi enim ad minim veniam, quis nostrud exerci tation ullamcorper suscipit lobortis nisl ut aliquip ex ea commodo consequat. Duis autem vel eum iriure dolor in hendrerit in vulputate velit esse molestie consequat, vel illum dolore eu feugiat nulla facilisis at vero eros et accumsan et iusto odio dignissim qui blandit praesent luptatum zzril delenit augue duis dolore te feugait nulla facilisi.</p>
<a class="abs btn" style="left:306px;top:450px;width:62px;height:18px">Read More ››</a>

<!-- products -->
<section class="abs products"></section>
<h2 class="abs section-title" style="top:519px;font-size:17.5px">OUR <em>PRODUCTS</em></h2>
<svg class="abs divider" style="top:549px" viewBox="0 0 64 8"><line x1="0" y1="4" x2="64" y2="4" stroke="#ccc"/><rect x="28" y="0" width="8" height="8" transform="rotate(45 32 4)" fill="#ddd"/></svg>

<svg class="abs chev" style="left:53px" width="12" height="22" viewBox="0 0 12 22"><path d="M10 2L2 11l8 9" fill="none" stroke="#f78f20" stroke-width="2.5"/></svg>
<svg class="abs chev" style="left:609px" width="12" height="22" viewBox="0 0 12 22"><path d="M2 2l8 9-8 9" fill="none" stroke="#f78f20" stroke-width="2.5"/></svg>

<article class="abs card" style="left:74px">
  <div class="card-photo" role="img" aria-label="Dark private cinema with tiered seating" style="background:linear-gradient(#1c2226,#3a3530 70%,#6a5240)"></div>
  <h3>Residential Cinemas</h3>
  <p>Lorem ipsum dolor sit amet, consectetuer ullamcorper suscipit lobortis nisl ut consequat ullamcorper.</p>
  <span class="plus"></span>
</article>
<article class="abs card" style="left:256px">
  <div class="card-photo" role="img" aria-label="Hand holding a remote controlling room lighting" style="background:linear-gradient(#f2f2f2,#c9c4bc 60%,#6f6a66)"></div>
  <h3>Automated Lighting Control</h3>
  <p>Lorem ipsum dolor sit amet, consectetuer ullamcorper suscipit lobortis nisl ut consequat ullamcorper.</p>
  <span class="plus"></span>
</article>
<article class="abs card" style="left:438px">
  <div class="card-photo" role="img" aria-label="Media room with speakers, TV and red chairs" style="background:linear-gradient(#ef8a1f,#f39a33 65%,#c94a2a)"></div>
  <h3>Outdoor Audio and Video</h3>
  <p>Lorem ipsum dolor sit amet, consectetuer ullamcorper suscipit lobortis nisl ut consequat ullamcorper.</p>
  <span class="plus"></span>
</article>
<a class="abs btn" style="left:301px;top:732px;width:63px;height:18px">View More ››</a>

<!-- past project -->
<h2 class="abs section-title" style="top:800px;font-size:17px;font-family:'Roboto Condensed',sans-serif">PAST <em>PROJECT</em></h2>
<svg class="abs divider" style="top:828px" viewBox="0 0 64 8"><line x1="0" y1="4" x2="64" y2="4" stroke="#ccc"/><rect x="28" y="0" width="8" height="8" transform="rotate(45 32 4)" fill="#ddd"/></svg>

<div class="abs tile" role="img" aria-label="Home theatre with blue cove lighting and large screen" style="left:0;top:862px;width:185px;height:160px;background:linear-gradient(#10263a,#5a3a22 60%,#1a1410)"></div>
<div class="abs tile" role="img" aria-label="Dark cinema room" style="left:187px;top:862px;width:133px;height:91px;background:#2a2a2a"></div>
<div class="abs" style="left:187px;top:862px;width:133px;height:91px;background:rgba(0,0,0,.55);color:#fff;text-align:center">
  <div style="margin-top:27px;font-family:'Roboto',sans-serif;font-weight:700;font-size:8px;letter-spacing:.3px">LOREM IPSUM DOLOR</div>
  <div style="margin-top:4px;font-size:6.2px;line-height:8.5px">Mauris ultrices lorem et felis<br>vehicula efficitur. Suspendisse<br>pellentesque.</div>
</div>
<div class="abs tile" role="img" aria-label="Cinema with tiered seating" style="left:187px;top:956px;width:133px;height:66px;background:linear-gradient(#1d2327,#5e4632)"></div>
<div class="abs tile" role="img" aria-label="Desk with two monitors" style="left:322px;top:862px;width:190px;height:74px;background:linear-gradient(135deg,#e6e6e6,#c05a40 55%,#9a9a9a)"></div>
<div class="abs tile" role="img" aria-label="Equipment rack" style="left:322px;top:938px;width:101px;height:84px;background:linear-gradient(#2b2b2b,#5a5a5a)"></div>
<div class="abs tile" role="img" aria-label="Built-in cabinet with AV components" style="left:426px;top:938px;width:86px;height:84px;background:linear-gradient(#d8c8b0,#efe8dc)"></div>
<div class="abs tile" role="img" aria-label="Ceiling-mounted projector" style="left:514px;top:862px;width:160px;height:160px;background:linear-gradient(135deg,#e9d8bf,#8a7a66 60%,#3a3a3a)"></div>

<!-- footer -->
<footer class="abs site-footer"></footer>
<div class="abs feedback">
  <h4>Feedback</h4>
  <div class="field" style="top:36px">Name</div>
  <div class="field" style="top:63px">Email</div>
  <a class="btn subscribe">Subscribe</a>
</div>
<div class="abs footer-col links">
  <h4>Quick Links</h4>
  <ul><li>Home</li><li>Feedback</li><li>Our Team</li><li>Contact Us</li><li>Services</li><li>Products</li><li>Past Project</li></ul>
</div>
<div class="abs footer-col contact"><h4>Contact Info</h4></div>
<div class="abs world-map" role="img" aria-label="World map background"></div>
<svg class="abs" style="left:462px;top:1084px" width="11" height="14" viewBox="0 0 11 14"><path d="M5.5 0A5 5 0 0 0 .5 5c0 4 5 9 5 9s5-5 5-9a5 5 0 0 0-5-5z" fill="#fff"/><circle cx="5.5" cy="5" r="2" fill="#111"/></svg>
<div class="abs address">123,Lorem Ipsum is simply dummy text of the printing</div>
<div class="abs contact-line" style="top:1120px">
  <svg width="10" height="10" viewBox="0 0 10 10"><path d="M1.5 1l2 .3.8 2-1 1c.6 1.2 1.4 2 2.6 2.6l1-1 2 .8.3 2C6 9 1 4 1.5 1z" fill="#fff"/></svg>
  <b style="font-weight:700">0123 4567 891</b>
</div>
<div class="abs contact-line" style="top:1138px">
  <svg width="10" height="8" viewBox="0 0 10 8"><rect x="0.5" y="0.5" width="9" height="7" fill="none" stroke="#fff"/><path d="M.5 .5L5 4.5 9.5 .5" fill="none" stroke="#fff"/></svg>
  info@rminstallations.example
</div>

<div class="abs bottom-bar"></div>
<span class="abs social dark" style="left:75px"></span>
<span class="abs social" style="left:99px"></span>
<span class="abs social" style="left:123px"></span>
<span class="abs social" style="left:147px"></span>
<p class="abs copyright">© 2015 RM Installations. All Rights Reserved.</p>

</body>
</html>
```